Business Card front and back

I am looking for business card design. I really really like the design file I uploaded named 627788_19250069_3478263_85f427ee_image

Target Market(s)

Corporate Fitness High end Private country club

Industry/Entity Type

Fitness Industry

Contact Information for Business Card

The last image I like as an example I uploaded a bunch of my logos. The file labeled "the signature" is my business card information for you to use

Colors
0054AA
0677BA
7BADD7
CADEEF
E8F1F8

Requirements
Must have
• E-mail sigThe file I uploaded labeled "627788_19250069_3478263_85f427ee_image" with all the plus signs on the back if those could be the logo symbol I uploaded labeled "1 back.png"

```html
<!DOCTYPE html>
<html lang="en">
<head>
<meta charset="utf-8">
<title>Summit Motion – Business Card</title>
<link rel="stylesheet" href="https://fonts.googleapis.com/css2?family=Montserrat:wght@400;500;800&display=swap">
<style>
  :root {
    --stage: #d4d4d4;
    --card-white: #ffffff;
    --ink: #2b2b2b;
    --band: #2f2f2f;
    --brand-blue: #4580c4;
    --back-dark: #232323;
    --back-mid: #2e2e2e;
    --back-light: #4a4a4a;
    --text-light: #f2f2f2;
  }
  * { box-sizing: border-box; margin: 0; padding: 0; }
  html, body {
    width: 1200px; height: 800px; overflow: hidden;
    background: var(--stage);
    font-family: "Montserrat", Arial, sans-serif;
  }
  .stage {
    width: 1200px; height: 800px;
    display: flex; align-items: center; justify-content: center; gap: 40px;
  }
  .card {
    position: relative; width: 540px; height: 310px;
    border-radius: 22px; overflow: hidden;
    border: 2px solid var(--brand-blue);
    box-shadow: 0 14px 30px rgba(0,0,0,0.25);
  }
  /* Front */
  .card-front { background: var(--card-white); }
  .brand {
    position: absolute; left: 30px; top: 42px;
    display: flex; align-items: center; gap: 12px;
  }
  .brand-dot { width: 30px; height: 30px; border-radius: 50%; background: var(--brand-blue); flex: none; }
  .brand-name {
    font-weight: 800; font-size: 24px; letter-spacing: 1px;
    color: var(--ink); text-transform: uppercase; white-space: nowrap;
  }
  .accent-block {
    position: absolute; right: 0; top: 34px; width: 140px; height: 70px;
    background: var(--brand-blue);
  }
  .contact-band {
    position: absolute; left: 0; top: 122px; width: 340px; height: 112px;
    background: var(--band);
    padding: 12px 0 0 28px;
    display: flex; flex-direction: column; gap: 5px;
  }
  .contact-row {
    display: flex; align-items: center; gap: 10px;
    color: var(--text-light); font-size: 13px; font-weight: 500; white-space: nowrap;
  }
  .contact-icon {
    width: 18px; height: 18px; border-radius: 50%;
    background: var(--brand-blue);
    display: flex; align-items: center; justify-content: center; flex: none;
  }
  .contact-icon svg { width: 11px; height: 11px; }
  .person { position: absolute; left: 30px; top: 250px; }
  .person-name { font-size: 24px; font-weight: 800; color: var(--ink); line-height: 1; white-space: nowrap; }
  .person-name .surname { color: var(--brand-blue); }
  .person-role { font-size: 15px; font-weight: 400; color: var(--ink); margin-top: 3px; }
  .portrait-frame {
    position: absolute; left: 360px; top: 60px; width: 150px; height: 178px;
    border: 2px solid var(--brand-blue); background: var(--card-white); padding: 4px;
  }
  .portrait {
    width: 100%; height: 100%;
    background: radial-gradient(circle at 55% 40%, #5a5550 0%, #2a2a2a 60%, #141414 100%);
  }
  /* Back */
  .card-back { background: var(--back-dark); }
  .back-pattern {
    position: absolute; inset: 0;
    background:
      repeating-linear-gradient(90deg, rgba(255,255,255,0.05) 0 44px, rgba(0,0,0,0) 44px 66px),
      repeating-linear-gradient(0deg, rgba(0,0,0,0.18) 0 12px, rgba(0,0,0,0) 12px 44px),
      linear-gradient(135deg, #121212 0%, var(--back-mid) 50%, var(--back-light) 100%);
  }
  .back-brand {
    position: absolute; left: 50%; top: 50%; transform: translate(-50%, -50%);
    display: flex; align-items: center; gap: 12px;
    padding: 10px 16px; background: var(--back-dark); border-radius: 6px;
  }
  .back-brand-square { width: 28px; height: 28px; background: var(--brand-blue); flex: none; }
  .back-brand-name {
    font-weight: 800; font-size: 26px; letter-spacing: 1px;
    color: var(--text-light); text-transform: uppercase; white-space: nowrap;
  }
</style>
</head>
<body>
<main class="stage">
  <section class="card card-front" aria-label="Business card front">
    <div class="accent-block"></div>
    <div class="brand">
      <span class="brand-dot"></span>
      <span class="brand-name">Summit Motion</span>
    </div>
    <div class="contact-band">
      <div class="contact-row">
        <span class="contact-icon"><svg viewBox="0 0 24 24" fill="#fff"><path d="M6.6 10.8a15 15 0 0 0 6.6 6.6l2.2-2.2c.3-.3.7-.4 1-.2 1.1.4 2.3.6 3.6.6.6 0 1 .4 1 1V20c0 .6-.4 1-1 1A17 17 0 0 1 3 4c0-.6.4-1 1-1h3.5c.6 0 1 .4 1 1 0 1.3.2 2.5.6 3.6.1.3 0 .7-.2 1z"/></svg></span>
        555-014-2270
      </div>
      <div class="contact-row">
        <span class="contact-icon"><svg viewBox="0 0 24 24" fill="none" stroke="#fff" stroke-width="2.4"><rect x="3" y="5" width="18" height="14"/><path d="M3 6l9 7 9-7"/></svg></span>
        dana@summitmotion.co
      </div>
      <div class="contact-row">
        <span class="contact-icon"><svg viewBox="0 0 24 24" fill="none" stroke="#fff" stroke-width="2.2"><circle cx="12" cy="12" r="9"/><path d="M3 12h18M12 3c3 3 3 15 0 18M12 3c-3 3-3 15 0 18"/></svg></span>
        www.summitmotion.co
      </div>
      <div class="contact-row">
        <span class="contact-icon"><svg viewBox="0 0 24 24" fill="#fff"><path d="M12 2a7 7 0 0 0-7 7c0 5 7 13 7 13s7-8 7-13a7 7 0 0 0-7-7zm0 9.5A2.5 2.5 0 1 1 12 6.5a2.5 2.5 0 0 1 0 5z"/></svg></span>
        OR.WA.ID.MT.WY
      </div>
    </div>
    <div class="person">
      <div class="person-name">DANA <span class="surname">CORVEL</span></div>
      <div class="person-role">Consultant</div>
    </div>
    <div class="portrait-frame">
      <div class="portrait" role="img" aria-label="Portrait photo of the consultant on a dark background"></div>
    </div>
  </section>

  <section class="card card-back" aria-label="Business card back">
    <div class="back-pattern" role="img" aria-label="Repeating brand pattern in rows, shading from black to grey"></div>
    <div class="back-brand">
      <span class="back-brand-square"></span>
      <span class="back-brand-name">Summit Motion</span>
    </div>
  </section>
</main>
</body>
</html>
```